SnackOrbit!!! A Vending Machine Business Looking for an attractive website.

We are a vending machine business in Northern Michigan. We have changed our name and have rebranded our company. We would like an attractive website that shares who we are, what services we provide, the products we offer in our machines, along with a form businesses can fill out to see if they are a good fit for our company. I would like to have a Home Page, About SnackOrbit, Why Choose SnackOrbit?, Products & Services, Contact Us (With a Login Option), and a page with a questionnaire for thos interested in getting a FREE Vending Machine.

Target Market(s)

Businesses, Campgrounds, Schools, and many more in Northern Michigan

Industry/Entity Type

Vending Machines

Coding

Coded - Design and coding required

Number of Pages Required

5+ page

Requirements
Must have
• An inviting and enticing Home Page. I want to get my potential clients engaged in our website.
Nice to have
• Possibly background photos from Northern Michigan
Should not have
• A corporate feel. I do not want a boring website.

```html
<!DOCTYPE html>
<html lang="en">
<head>
<meta charset="utf-8">
<title>SnackOrbit – Crave. Vend. Repeat.</title>
<link rel="stylesheet" href="https://fonts.googleapis.com/css2?family=Anton&family=Roboto:wght@400;500;700&display=swap">
<style>
:root{
  --navy:#13115c;
  --navy-deep:#0d0b4a;
  --green:#2b5a23;
  --mint:#c6efb4;
  --ink:#1a1a1a;
  --grey:#6b6b6b;
  --field:#f1f1f1;
  --pale:#e4e7e3;
  --white:#ffffff;
}
*{box-sizing:border-box;margin:0;padding:0}
html,body{width:1200px;height:3866px;overflow:hidden}
body{position:relative;font-family:'Roboto',sans-serif;color:var(--ink);background:var(--white)}
.abs{position:absolute}
.display{font-family:'Anton',sans-serif;font-weight:400;letter-spacing:.5px}
.btn{position:absolute;display:flex;align-items:center;justify-content:center;gap:7px;border-radius:22px;font:700 13px 'Roboto',sans-serif;text-transform:uppercase;color:var(--white)}
.btn .dot{width:12px;height:12px;border-radius:50%;background:currentColor;position:relative}
.btn .dot::after{content:"";position:absolute;left:3px;top:3px;border-left:6px solid var(--navy);border-top:3px solid transparent;border-bottom:3px solid transparent}
.btn.green .dot::after{border-left-color:var(--green)}
.btn.green{background:var(--green)}
.btn.navy{background:var(--navy)}
.btn.navy .dot::after{border-left-color:var(--navy)}
.btn.outline{border:2px solid var(--white);background:transparent}
.btn.light{background:var(--white);color:var(--navy);border:1px solid #ccc}
.btn.light .dot::after{border-left-color:var(--white)}
.logo-word{font:700 34px 'Roboto',sans-serif;color:var(--navy);display:flex;align-items:center;gap:8px}
.logo-word .mark{width:14px;height:14px;background:var(--green);border-radius:50%}

/* header */
.topbar{left:540px;top:0;width:660px;height:44px;background:var(--navy);clip-path:polygon(25px 0,100% 0,100% 100%,50px 100%)}
.topbar span{position:absolute;top:10px;color:var(--white);font:500 18px 'Roboto',sans-serif;display:flex;align-items:center;gap:10px}
.free{left:330px;top:22px;font:700 13px 'Roboto',sans-serif;color:var(--navy)}
.nav{left:322px;top:72px;display:flex;gap:34px;font:500 14px 'Roboto',sans-serif;color:var(--ink)}
.user{left:1048px;top:62px;width:37px;height:37px;border-radius:50%;background:var(--green)}

/* section titles */
.title{width:1200px;text-align:center;font-family:'Anton',sans-serif;font-size:38px;color:var(--ink)}
.title.white{color:var(--white)}
.rule{left:565px;width:70px;height:4px;background:var(--green)}
.rule.white{background:var(--white)}
.para{text-align:center;color:var(--grey);font-size:14px;line-height:26px}

.card{position:absolute;width:230px;height:255px;background:#c9c9d2;border-radius:6px;padding:10px}
.card .ph{width:100%;height:235px;border-radius:4px}
.card .lbl{position:absolute;left:0;width:100%;bottom:38px;text-align:center;color:var(--white);font:700 14px 'Roboto',sans-serif;text-transform:uppercase}
.card .go{position:absolute;right:-12px;bottom:-12px;width:40px;height:40px;border-radius:50%;background:var(--white);border:5px solid var(--navy);display:flex;align-items:center;justify-content:center;font-size:14px;color:var(--navy)}
.arrow{position:absolute;width:36px;height:36px;border-radius:50%;background:var(--white);color:var(--navy);display:flex;align-items:center;justify-content:center;font-size:16px;top:1592px}

.why{position:absolute;top:2100px;width:220px;height:400px;border-radius:110px;background:#f3f3f6;border:1px solid #e0e0ea;text-align:center}
.why .ic{width:152px;height:152px;border-radius:50%;margin:24px auto 0;display:flex;align-items:center;justify-content:center}
.why h3{margin-top:28px;font:700 14px 'Roboto',sans-serif;text-transform:uppercase}
.why p{margin:14px 22px 0;font-size:12.5px;line-height:21px;color:var(--grey)}
.why a{display:block;margin-top:18px;font:700 12px 'Roboto',sans-serif;color:var(--navy);text-decoration:underline}
.why.dark{background:var(--navy)}
.why.dark h3,.why.dark p,.why.dark a{color:var(--white)}
.ring{position:absolute;top:2085px;width:240px;height:430px;border-radius:120px;border:2px dotted var(--navy)}

.field{position:absolute;background:var(--field);border-radius:22px;font-size:13px;color:#666;padding:14px 20px}

.foot{color:var(--white);font-size:13px;line-height:26px}
.foot h4{font:700 13px 'Roboto',sans-serif;margin-bottom:6px}
.soc{width:32px;height:32px;border-radius:50%;background:var(--white);display:inline-block;margin-right:7px}
</style>
</head>
<body>

<!-- header -->
<header>
  <div class="abs topbar">
    <span style="left:100px">&#9993; info@snackorbit.com</span>
    <span style="left:395px">&#9742; +1 (555) 010 0199</span>
  </div>
  <div class="abs free">GET A FREE VENDING MACHINE</div>
  <div class="abs logo-word" style="left:112px;top:48px"><span class="mark"></span>SnackOrbit</div>
  <nav class="abs nav"><span>Home</span><span>About SnackOrbit</span><span>Why Choose SnackOrbit?</span><span>Products &amp; Services</span></nav>
  <div class="btn green" style="left:890px;top:62px;width:146px;height:38px">Contact Us <span class="dot"></span></div>
  <div class="abs user"></div>
</header>

<!-- hero -->
<svg class="abs" style="left:0;top:115px" width="1200" height="650" viewBox="0 0 1200 650">
  <rect width="1200" height="650" fill="#13115c"/>
  <polygon points="0,600 1200,430 1200,650 0,650" fill="#2b5a23"/>
  <polygon points="600,520 1200,440 1200,600" fill="#e4e7e3"/>
  <polygon points="0,645 1200,600 1200,650 0,650" fill="#ffffff"/>
  <polygon points="0,650 0,640 1200,610 1200,650" fill="#ffffff"/>
</svg>
<svg class="abs" style="left:0;top:640px" width="1200" height="125"><polygon points="0,120 1200,0 1200,125 0,125" fill="#fff"/></svg>
<div class="abs display" style="left:108px;top:245px;font-size:54px;color:#fff">SnackOrbit</div>
<div class="abs display" style="left:108px;top:322px;font-size:54px;color:#fff"><span style="color:var(--mint)">Crave.</span> Vend. Repeat.</div>
<div class="abs" style="left:107px;top:418px;font:700 23px 'Roboto',sans-serif;color:#fff">ELEVATING SNACKING, ONE VEND AT A TIME</div>
<div class="btn outline" style="left:109px;top:482px;width:146px;height:37px">Get Stasrted <span class="dot"></span></div>
<div class="abs" role="img" aria-label="Three colourful vending machines stocked with snacks and drinks" style="left:665px;top:296px;width:535px;height:318px;background:linear-gradient(90deg,#4a4670 0 27%,transparent 27% 34%,#e8284a 34% 61%,transparent 61% 69%,#f29b18 69%);border-radius:8px"></div>

<!-- about -->
<div class="abs title" style="top:705px">About SnackOrbit</div>
<p class="abs para" style="left:325px;top:793px;width:550px">At SnackOrbit, we don't just vend snacks—we curate cravings. Our customized vending solutions bring flavor, convenience, and community to Northern Michigan. Whether you're reaching for a mid-morning snack, a refreshing beverage, or a satisfying breakfast burrito, SnackOrbit delivers delight with every bite</p>
<div class="btn green" style="left:527px;top:924px;width:146px;height:38px">View More <span class="dot"></span></div>

<!-- lighthouse band -->
<div class="abs" role="img" aria-label="Northern Michigan lighthouse on a pier at sunset over the lake" style="left:0;top:958px;width:1200px;height:420px;background:linear-gradient(180deg,#ffffff 0%,#c9c8d6 28%,#8e7e9a 48%,#e37a56 66%,#f29a52 74%,#5b4a66 88%,#3a3350 100%)"></div>
<svg class="abs" style="left:0;top:1240px" width="1200" height="100"><polygon points="0,30 0,100 1200,100 1200,0" fill="#e4e7e3" opacity=".0"/></svg>

<!-- products -->
<svg class="abs" style="left:0;top:1240px" width="1200" height="685" viewBox="0 0 1200 685">
  <polygon points="0,130 1200,0 1200,675 0,680" fill="#13115c"/>
  <polygon points="0,130 440,80 0,55" fill="#ffffff" opacity=".9"/>
</svg>
<div class="abs title white" style="top:1373px">Our Products</div>
<div class="abs rule white" style="top:1430px"></div>
<div class="arrow" style="left:50px">&#8249;</div>
<div class="arrow" style="left:1114px">&#8250;</div>
<div class="card" style="left:110px;top:1482px"><div class="ph" role="img" aria-label="Drink cooler full of bottled beverages" style="background:linear-gradient(180deg,#e9e2d4,#c7583c 55%,#3e3a3a)"></div><div class="lbl">Beverages</div><div class="go">&#8250;</div></div>
<div class="card" style="left:358px;top:1499px"><div class="ph" role="img" aria-label="Chocolate candy bars" style="background:linear-gradient(135deg,#2c2a2a,#b8242a 55%,#1d1b1b)"></div><div class="lbl">Sweets</div><div class="go">&#8250;</div></div>
<div class="card" style="left:606px;top:1482px"><div class="ph" role="img" aria-label="Bags of almonds, cashews and dried fruit" style="background:linear-gradient(180deg,#2a2420,#b88655 50%,#7a3a2a)"></div><div class="lbl">Nuts &amp; Fruits</div><div class="go">&#8250;</div></div>
<div class="card" style="left:855px;top:1465px"><div class="ph" role="img" aria-label="Snack vending machine stocked with bars" style="background:linear-gradient(180deg,#1f1f22,#5b6a55 50%,#1b1b1e)"></div><div class="lbl">Snacks Bars</div><div class="go">&#8250;</div></div>
<div class="btn outline" style="left:527px;top:1798px;width:146px;height:38px">View More <span class="dot"></span></div>

<!-- why choose -->
<div class="abs title" style="top:2002px">Why Choose SnackOrbit?</div>
<div class="abs rule" style="top:2061px"></div>
<div class="ring" style="left:90px"></div>
<div class="ring" style="left:350px"></div>
<div class="ring" style="left:610px"></div>
<div class="ring" style="left:870px"></div>
<div class="why" style="left:100px"><div class="ic" style="background:var(--navy)"><svg width="60" height="60" viewBox="0 0 24 24" fill="none" stroke="#fff" stroke-width="1.3"><path d="M12 20s-7-4.5-7-10a4 4 0 0 1 7-2.5A4 4 0 0 1 19 10c0 5.5-7 10-7 10z"/></svg></div><h3>Local Love</h3><p>At SnackOrbit, we're more than vending machines; we're flavor architects, community connectors, and taste</p><a>VIEW MORE</a></div>
<div class="why" style="left:360px"><div class="ic" style="background:var(--green)"><svg width="50" height="70" viewBox="0 0 20 28" fill="none" stroke="#fff" stroke-width="1.2"><rect x="2" y="1" width="16" height="26" rx="1"/><rect x="4" y="4" width="8" height="16"/><line x1="14" y1="5" x2="16" y2="5"/><line x1="14" y1="8" x2="16" y2="8"/><rect x="5" y="22" width="10" height="3"/></svg></div><h3>Unleash Your Cravings</h3><p>SnackOrbit isn't bound by corporate ties. We're the rebels of the vending world. Craving</p><a>VIEW MORE</a></div>
<div class="why dark" style="left:620px"><div class="ic" style="border:2px solid #fff"><svg width="70" height="70" viewBox="0 0 24 24" fill="none" stroke="#fff" stroke-width="1.2"><circle cx="12" cy="12" r="9"/><circle cx="12" cy="12" r="6"/><path d="M9 12l2 2 4-4"/></svg></div><h3>Quality Meets</h3><p>magine this: You're mid-meeting, and your stomach growls. Fear not! SnackOrbit's</p><a>VIEW MORE</a></div>
<div class="why" style="left:880px"><div class="ic" style="background:var(--green)"><svg width="70" height="70" viewBox="0 0 24 24" fill="none" stroke="#fff" stroke-width="1.2"><circle cx="12" cy="12" r="4"/><path d="M12 8V3M12 16v5M8 12H3M16 12h5M9 9 5.5 5.5M15 15l3.5 3.5M15 9l3.5-3.5M9 15l-3.5 3.5"/></svg></div><h3>Pandemic-Proof</h3><p>Life throws curveballs, but SnackOrbit stands strong. Our vending machines are the unsung heroes of resilience.</p><a>VIEW MORE</a></div>

<!-- call to action -->
<svg class="abs" style="left:0;top:2575px" width="1200" height="460" viewBox="0 0 1200 460"><polygon points="0,30 1200,0 1200,450 0,390" fill="#13115c"/></svg>
<div class="abs title white" style="top:2672px">Ready To Experience The SnackOrbit Difference?</div>
<p class="abs para" style="left:300px;top:2765px;width:600px;color:#fff">Sign up now and let's connect. Taste the future of snacking firsthand! Contact us today and explore how our vending magic can elevate your space.</p>
<div class="abs" style="left:250px;top:2852px;width:700px;height:58px;border-radius:29px;background:#fff"></div>
<div class="abs" style="left:296px;top:2870px;width:428px;border-bottom:1px solid #aaa;padding-bottom:4px;font-size:14px;color:#555">Enter Email Address</div>
<div class="btn navy" style="left:786px;top:2862px;width:142px;height:36px">Sign Up <span class="dot"></span></div>

<!-- contact -->
<div class="abs title" style="top:3035px">Contact Us</div>
<div class="field" style="left:315px;top:3130px;width:270px;height:42px;padding-top:12px">Name</div>
<div class="field" style="left:315px;top:3186px;width:270px;height:42px;padding-top:12px">Email</div>
<div class="field" style="left:315px;top:3242px;width:270px;height:42px;padding-top:12px">Phone</div>
<div class="field" style="left:597px;top:3130px;width:308px;height:155px;border-radius:16px">Message</div>
<div class="btn navy" style="left:528px;top:3307px;width:144px;height:36px">Submit <span class="dot"></span></div>

<!-- footer -->
<svg class="abs" style="left:0;top:3375px" width="1200" height="491" viewBox="0 0 1200 491"><polygon points="0,0 1200,30 1200,491 0,491" fill="#2b5a23"/><polygon points="0,40 1200,55 1200,491 0,491" fill="#000"/><polygon points="480,38 750,38 730,130 500,130" fill="#fff"/></svg>
<div class="abs logo-word" style="left:518px;top:3440px;font-size:32px"><span class="mark"></span>SnackOrbit</div>
<div class="abs foot" style="left:114px;top:3577px;width:210px">Lorem ipsum dolor sit amet, consectetur adipiscing elit, sed do eiusmod tempor incididunt ut labore et dolore magna aliqua. Ut enim ad minim veniam, quis nostrud</div>
<div class="abs foot" style="left:402px;top:3574px"><h4>QUICK LINKS</h4>Home<br>About<br>Service<br>Products<br>FAQ<br>Log in</div>
<div class="abs foot" style="left:590px;top:3574px;width:190px"><h4>CONTACT US</h4>Lorem ipsum dolor sit amet, consectetur adipiscing elit, sed do eiusmod<div style="margin-top:10px">&#9742; +1 (555) 010 0199</div><div style="margin-top:8px">&#9993; info@snackorbit.com</div></div>
<div class="abs foot" style="left:882px;top:3575px;width:240px">INTERESTED IN GETTING A FREE VENDING MACHINE</div>
<div class="btn light" style="left:882px;top:3641px;width:146px;height:38px">Visit Now <span class="dot" style="color:var(--navy)"></span></div>
<div class="abs" style="left:893px;top:3704px"><span class="soc"></span><span class="soc"></span><span class="soc"></span></div>
<div class="abs foot" style="left:0;top:3800px;width:1200px;text-align:center;font-size:12px">Copyright@2024 - All Rights Reserved By SnackOrbit</div>

</body>
</html>
```